Business card design

Hi,
I need to have a business card design based on the current logo.
If competitive I not put it out to everyone.

It can be single of double sided

Target Market(s)

Food businesses

Industry/Entity Type

Food Manufacturing

Contact Information for Business Card

Details will on card will be as follows Name = Marcus Bell Email = Marcus@PanHearth.com.au Phone = 0418563207 Address = 57 Larkin Street , Fortitude Valley QLD 4006 Australia

Font styles to use
Other font styles liked:
• based on two fonts - Adelle & Museo

Requirements
Must have
• Based on the on switch concept

```html
<!DOCTYPE html>
<html lang="en">
<head>
<meta charset="utf-8">
<title>PanHearth Business Card</title>
<link rel="stylesheet" href="https://fonts.googleapis.com/css2?family=Montserrat:wght@500;600;700&family=Zilla+Slab:wght@500&display=swap">
<style>
  :root {
    --stage: #9a9a9a;
    --paper: #ffffff;
    --brand-red: #ee2a4a;
    --brand-dark: #3a2124;
    --back-dark: #382023;
    --ink: #4a4a4a;
    --light: #ffffff;
  }
  html, body {
    margin: 0;
    padding: 0;
    width: 1133px;
    height: 1200px;
    overflow: hidden;
    background: var(--stage);
  }
  .card {
    position: absolute;
    left: 205px;
    width: 724px;
    height: 412px;
    border-radius: 26px;
    overflow: hidden;
    font-family: "Montserrat", sans-serif;
  }
  .card--front { top: 141px; background: var(--paper); }
  .card--back { top: 645px; background: var(--back-dark); }

  .front-curves { position: absolute; inset: 0; }

  .wordmark {
    position: absolute;
    left: 53px;
    top: 62px;
    display: flex;
    align-items: center;
    gap: 12px;
  }
  .wordmark__dot {
    width: 40px;
    height: 40px;
    border-radius: 50%;
    background: var(--brand-red);
  }
  .wordmark__name {
    font-weight: 600;
    font-size: 46px;
    letter-spacing: 1px;
    color: var(--brand-dark);
    line-height: 1;
  }
  .tagline {
    position: absolute;
    left: 0;
    width: 408px;
    top: 118px;
    text-align: right;
    font-family: "Zilla Slab", serif;
    font-weight: 500;
    font-size: 16px;
    color: var(--brand-dark);
  }

  .address {
    position: absolute;
    left: 53px;
    top: 228px;
    margin: 0;
    font-style: normal;
    font-weight: 500;
    font-size: 16px;
    line-height: 20.5px;
    color: var(--ink);
  }
  .contacts {
    position: absolute;
    left: 53px;
    top: 298px;
    margin: 0;
    padding: 0;
    list-style: none;
    font-weight: 500;
    font-size: 16px;
    line-height: 20.5px;
    color: var(--ink);
  }
  .contacts li { display: flex; align-items: center; gap: 9px; }
  .contacts svg { width: 13px; height: 13px; flex: none; }

  .holder-name {
    position: absolute;
    right: 52px;
    top: 346px;
    margin: 0;
    font-weight: 700;
    font-size: 22px;
    letter-spacing: 0.5px;
    color: var(--light);
  }

  .back-mark {
    position: absolute;
    left: 0;
    right: 0;
    top: 180px;
    display: flex;
    justify-content: center;
    align-items: center;
    gap: 16px;
  }
  .back-mark__dot {
    width: 52px;
    height: 52px;
    border-radius: 50%;
    background: var(--brand-red);
  }
  .back-mark__name {
    font-weight: 600;
    font-size: 52px;
    letter-spacing: 1px;
    color: var(--light);
    line-height: 1;
  }
  .back-url {
    position: absolute;
    left: 0;
    right: 0;
    top: 353px;
    text-align: center;
    font-weight: 500;
    font-size: 16px;
    letter-spacing: 3.5px;
    color: var(--light);
  }
</style>
</head>
<body>
  <section class="card card--front">
    <svg class="front-curves" viewBox="0 0 724 412" width="724" height="412" aria-hidden="true">
      <path fill="var(--brand-dark)" d="M622,0 C612,180 480,340 244,412 L300,412 C520,340 626,190 630,0 Z"/>
      <path fill="var(--brand-red)" d="M676,0 C652,190 520,350 322,412 L724,412 L724,0 Z"/>
    </svg>

    <div class="wordmark">
      <span class="wordmark__dot"></span>
      <span class="wordmark__name">PANHEARTH</span>
    </div>
    <div class="tagline">Fresh Kitchen Supply On Call</div>

    <address class="address">
      57 Larkin Street<br>
      Harlow Bay<br>
      QLD 4187 Australia
    </address>

    <ul class="contacts">
      <li>
        <svg viewBox="0 0 16 16" aria-hidden="true"><path fill="var(--brand-red)" d="M3.6 1 L6 4.2 L4.6 6 C5.6 8.2 7.6 10.2 9.9 11.3 L11.7 9.9 L15 12.3 L13.4 15 C7.2 14.6 1.4 8.8 1 2.6 Z"/></svg>
        0418563207
      </li>
      <li>
        <svg viewBox="0 0 16 16" aria-hidden="true"><rect x="1" y="3" width="14" height="10" rx="1" fill="var(--brand-red)"/><path d="M2 4 L8 9 L14 4" stroke="#fff" stroke-width="1.4" fill="none"/></svg>
        Marcus@PanHearth.com.au
      </li>
      <li>
        <svg viewBox="0 0 16 16" aria-hidden="true"><circle cx="8" cy="8" r="7" fill="var(--brand-red)"/><path d="M5 4 C7 5 6 7 8 8 C9 9 8 11 9 13 M10 3 C11 5 13 5 14 7" stroke="#fff" stroke-width="1.3" fill="none"/></svg>
        PanHearth.com.au
      </li>
    </ul>

    <p class="holder-name">MARCUS BELL</p>
  </section>

  <section class="card card--back">
    <div class="back-mark">
      <span class="back-mark__dot"></span>
      <span class="back-mark__name">PANHEARTH</span>
    </div>
    <div class="back-url">www.PanHearth.com.au</div>
  </section>
</body>
</html>
```